Brochure for The Harborline Group, insurance consultants

We need a more professional looking brochure for our managers to be able to leave behind with potential clients they meet with. This brochure needs to summarize all the services and value that The Harborline Group has to offer, pretty much giving an overview of the company.
The clients we deal with are Funeral Homes and Funeral Directors, we are an organization dedicated to assisting funeral homes in implementing highly profitable insurance programs while providing the training, support and service along the way. More information is provided in the brochure attached.
We are going for a professional simple theme, we want to get the message across without overwhelming the client.
This brochure needs to be a Tri-Fold, Landscaped format.
I have attached our current brochure design as reference and more information about the our company and what we offer. This one is obviously what we are looking to replace, but the information will be generally the same. It needs to be more visually appealing and maybe consolidate some of the information so it's not just a block of text.
Color: We would like to keep the color scheme in the White, Blue, Grey, Black spectrum
I have also attached our logo and Business Card
Target Market(s)
The target market for this brochure will be Funeral Directors and Funeral Homes. This brochure will be left behind with the potential clients as an overview of the services The Harborline Group has to offer.
Industry/Entity Type
Insurance
Look and feel

```html
<!DOCTYPE html>
<html lang="en">
<head>
<meta charset="utf-8">
<title>The Harborline Group – Tri-Fold Brochure</title>
<link rel="stylesheet" href="https://fonts.googleapis.com/css2?family=Tinos:ital,wght@0,400;0,700;1,400&display=swap">
<style>
:root{
  --backdrop:#2a2a2a;
  --blue-deep:#0b3fae;
  --blue-mid:#1f63d8;
  --blue-light:#3b86ee;
  --navy:#1d2f63;
  --paper:#ffffff;
  --paper-grey:#efefef;
  --ink:#3a3a3a;
  --cyan:#19a4d8;
  --gold:#f3c21a;
  --table-head:#2aa6e2;
  --placeholder-a:#c9ccd1;
  --placeholder-b:#9aa6b6;
}
*{margin:0;padding:0;box-sizing:border-box}
html,body{width:1200px;height:498px;overflow:hidden;background:var(--backdrop)}
body{font-family:"Tinos","Times New Roman",serif;position:relative}
.sheet{position:absolute;top:28px;height:442px;overflow:hidden;box-shadow:0 0 12px rgba(0,0,0,.6)}
.sheet--outside{left:13px;width:577px}
.sheet--inside{left:613px;width:572px}
.panel{position:absolute;top:0;height:442px;overflow:hidden}
.blue-field{position:absolute;background:linear-gradient(160deg,var(--blue-light) 0%,var(--blue-mid) 45%,var(--blue-deep) 100%);color:#fff}
.blue-field::after{content:"";position:absolute;left:-40%;top:30%;width:180%;height:90%;border-radius:50%;border-top:40px solid rgba(255,255,255,.07);pointer-events:none}
.blue-field>*{position:relative;z-index:1}
.photo{position:absolute;left:0;width:100%;background:linear-gradient(160deg,var(--placeholder-a),var(--placeholder-b))}
.heading{font-weight:700;font-variant:small-caps;letter-spacing:.4px;font-size:12px;white-space:nowrap}
.body-text{font-size:9px;line-height:1.55}
.rule{height:1px;background:rgba(255,255,255,.55)}
.wordmark{font-size:19px;letter-spacing:-.3px;white-space:nowrap}

/* outside */
.cover-about{left:0;width:180px}
.cover-about .photo{top:0;height:177px}
.cover-about .blue-field{top:177px;left:0;width:180px;height:265px;padding:16px 9px 0 9px}
.cover-about .heading{margin:6px 0 7px}
.cover-about .body-text{text-align:justify;line-height:1.6}
.cover-about .body-text+.body-text{margin-top:13px}

.cover-contact{left:180px;width:190px;background:linear-gradient(180deg,var(--paper) 0%,var(--paper-grey) 100%)}
.cover-contact .wordmark{position:absolute;top:102px;left:0;width:190px;text-align:center;color:var(--navy);font-size:18px}
.contact-list{position:absolute;top:346px;left:0;width:190px;text-align:center;color:var(--ink);font-size:10px;line-height:2.05}

.cover-front{left:370px;width:207px}
.cover-front .photo{top:0;height:259px}
.cover-front .blue-field{top:259px;left:0;width:207px;height:183px}
.cover-front .wordmark{position:absolute;top:24px;left:0;width:207px;text-align:center;color:#fff}
.cover-front .rule{position:absolute;top:48px;left:18px;width:170px}
.tagline{position:absolute;top:86px;left:26px;color:#fff;font-size:21px;letter-spacing:.5px}
.tagline span{display:block;font-size:13px;margin:10px 0 0 20px;letter-spacing:.3px}

/* inside */
.inside-alt{left:0;width:193px}
.inside-alt .blue-field{top:0;left:0;width:193px;height:294px;padding:16px 10px 0 10px}
.inside-alt .heading{font-size:11px}
.inside-alt .rule{margin:5px 0 9px}
.inside-alt .body-text{text-align:justify;font-size:8.6px;line-height:1.62}
.inside-alt .body-text+.body-text{margin-top:10px}
.inside-alt .photo{top:294px;height:148px}

.inside-rates{left:193px;width:189px;background:var(--paper);color:var(--ink)}
.rate-table{position:absolute;left:10px;width:174px;border-collapse:collapse;font-size:6px;background:#fff;box-shadow:0 0 2px rgba(0,0,0,.25)}
.rate-table th{background:var(--table-head);color:#fff;font-weight:400;padding:3px 1px;line-height:1.3;border-right:1px solid rgba(255,255,255,.6)}
.rate-table td{text-align:center;padding:4px 1px;border-top:1px solid #e6e6e6}
.rate-table--monthly{top:12px}
.rate-table--single{top:134px}
.rate-note{position:absolute;top:236px;left:10px;font-size:5.5px;color:#666}
.inside-rates .heading{position:absolute;top:266px;left:10px;font-size:11px;color:var(--ink)}
.inside-rates .divider{position:absolute;top:283px;left:10px;width:170px;height:1px;background:#cfcfcf}
.compare{position:absolute;top:290px;left:10px;width:172px;font-size:8.4px;line-height:1.55;text-align:justify}
.quote{position:absolute;top:338px;left:10px;width:172px;color:var(--cyan);font-style:italic;font-size:9px;line-height:1.4}
.closing{position:absolute;top:392px;left:10px;width:172px;font-size:8.2px;line-height:1.55}

.inside-offer{left:382px;width:190px}
.inside-offer .blue-field{top:0;left:0;width:190px;height:294px;padding:12px 10px 0 10px}
.inside-offer .heading{font-size:11px}
.inside-offer .rule{margin:6px 0 9px}
.inside-offer .body-text{font-size:8.4px;line-height:1.42;margin-bottom:8px}
.sub-heading{color:var(--gold);font-size:9.6px;margin:2px 0 6px}
.inside-offer .photo{top:294px;height:148px}
</style>
</head>
<body>

<section class="sheet sheet--outside" aria-label="Brochure outside">
  <div class="panel cover-about">
    <div class="photo" role="img" aria-label="Photo of a consultant meeting with a couple at a desk"></div>
    <div class="blue-field">
      <div class="rule"></div>
      <h2 class="heading">A Little About Us</h2>
      <div class="rule" style="margin-bottom:10px"></div>
      <p class="body-text">The Harborline Group is a nationwide organization dedicated to assisting funeral homes in implementing highly profitable insurance programs helping clients capturing wider markets and increasing the number of funerals taken care of each year.</p>
      <p class="body-text">One of our professional insurance experts will provide you live in person service and support at no cost throughout your relationship with The Harborline Group.<br>We are dedicated to the success of our clients and tailor our services to fit your needs.</p>
    </div>
  </div>

  <div class="panel cover-contact">
    <div class="wordmark">The Harborline Group</div>
    <p class="contact-list">(919) 555-0142<br>contracting@theharborlinegroup.com<br>www.theharborlinegroup.com</p>
  </div>

  <div class="panel cover-front">
    <div class="photo" role="img" aria-label="Photo placeholder: road leading toward the horizon under an open sky"></div>
    <div class="blue-field">
      <div class="wordmark">The Harborline Group</div>
      <div class="rule"></div>
      <p class="tagline">STRATEGY<span>MOVING FORWARD</span></p>
    </div>
  </div>
</section>

<section class="sheet sheet--inside" aria-label="Brochure inside">
  <div class="panel inside-alt">
    <div class="blue-field">
      <h2 class="heading">Provide A Better Alternative</h2>
      <div class="rule"></div>
      <p class="body-text">Our Final Expense products provide a better value to your customers by covering every cost associated with their funeral as opposed to being limited with pre-need coverage. Your clients will be able to purchase additional services such as flowers, memoirs, and everything else pre need will not cover.<br>Lower monthly payments on the policies allow you to reach a larger number of people who would otherwise not be able to afford the funeral they deserve.</p>
      <p class="body-text">Because our products have a significantly lower payment schedule compared to pre-need, your clients will have a much easier time making payments reducing the number of lapsed policies.</p>
    </div>
    <div class="photo" role="img" aria-label="Illustration of a man seen from behind looking at a rising bar chart sketch"></div>
  </div>

  <div class="panel inside-rates">
    <table class="rate-table rate-table--monthly">
      <tr><th>Age</th><th>Face Value</th><th>Male Pre Needs 5yrs</th><th>Final Expense Male</th><th>Female Pre Needs 5yrs</th><th>Final Expense Male</th></tr>
      <tr><td>65</td><td>$10,000</td><td>$230</td><td>$53</td><td>$230</td><td>$41</td></tr>
      <tr><td>70</td><td>$10,000</td><td>$247</td><td>$68</td><td>$247</td><td>$52</td></tr>
      <tr><td>75</td><td>$10,000</td><td>$275</td><td>$98</td><td>$275</td><td>$71</td></tr>
      <tr><td>80</td><td>$10,000</td><td>$422</td><td>$145</td><td>$422</td><td>$103</td></tr>
    </table>
    <table class="rate-table rate-table--single">
      <tr><th>Age</th><th>Pre Needs Single Pay</th><th>Final Expense Single Pay(M)</th><th>Final Expense Single Pay(M)</th></tr>
      <tr><td>65</td><td>$10,810</td><td>$15,545</td><td>$17,509</td></tr>
      <tr><td>70</td><td>$10,526</td><td>$13,653</td><td>$15,675</td></tr>
      <tr><td>75</td><td>$10,309</td><td>$12,401</td><td>$13,664</td></tr>
      <tr><td>80</td><td>$10,256</td><td>$11,238</td><td>$12,497</td></tr>
    </table>
    <p class="rate-note">*Rates subject to change</p>
    <h2 class="heading">See The Difference</h2>
    <div class="divider"></div>
    <p class="compare">This rate chart above shows the dramatic contrast between expensive pre-need payments and our cheaper alternative option.</p>
    <p class="quote">“A typical pre need payment is about the same as car payment, while a final expense payment is closer to a tank of gas”</p>
    <p class="closing">Provide a much greater value to your customer giving them options they can afford.</p>
  </div>

  <div class="panel inside-offer">
    <div class="blue-field">
      <h2 class="heading">Key Offerings</h2>
      <div class="rule"></div>
      <p class="body-text">Provide your clients alternative options for the costs of burial</p>
      <p class="body-text">We consult with you on maximizing revenue streams from insurance sales and bonuses</p>
      <p class="body-text">We provide full support and training for all your insurance related needs at no cost to you</p>
      <p class="sub-heading">Stop leaving business on the table</p>
      <p class="body-text">By providing a cheaper alternative to Pre Need, you open up the opportunity to help out lower income families that are unable to afford expensive pre need options.</p>
      <p class="sub-heading">Referral Bonus Program</p>
      <p class="body-text">Take advantage of our referral bonus program by introducing us to other funeral directors or funeral homes. Your representative will be able to explain this</p>
    </div>
    <div class="photo" role="img" aria-label="Photo of business people shaking hands in an office"></div>
  </div>
</section>

</body>
</html>
```